Dorwin's Coating & Renewal Letterhead Design We want to revamp out old traditional letterhead with the new logo designs that are attached. We are working on getting all our company items from vehicles, business, cards, t-shirts, letterhead to match. This should include company colors, fonts, and flow of items that we have attached below.

Industry/Entity Type

Construction Company

Font styles to use
Sans Serif
Other font styles liked:
• Bold with outline

Colors
ec1f27
ffffff

Requirements
Must have
• Company Name: Dorwin's Coating & Renewal
• Address: 4728 SW 81st Ter Halverd cove fl 39417
• Office Number: (555) 413-2986
• Email: Dorwinrenewal@mailbrook.example
• License Number: KRT8046392
Nice to have
• Company Colors: red, white, black, and grey

```html
<!DOCTYPE html>
<html lang="en">
<head>
<meta charset="utf-8">
<title>Dorwin's Coating &amp; Renewal – Letterhead</title>
<link rel="stylesheet" href="https://fonts.googleapis.com/css2?family=Lato:wght@400;900&display=swap">
<style>
  :root {
    --brand-red: #ec1f27;
    --paper: #ffffff;
    --ink: #1a1a1a;
    --backdrop: #e4dedc;
    --mark-red: rgba(236, 31, 39, 0.06);
    --mark-grey: rgba(120, 120, 120, 0.07);
  }
  * { box-sizing: border-box; margin: 0; padding: 0; }
  html, body {
    width: 1200px;
    height: 784px;
    overflow: hidden;
    background: var(--backdrop);
    font-family: "Lato", sans-serif;
  }
  .letterhead {
    position: absolute;
    left: 314px;
    top: 22px;
    width: 572px;
    height: 740px;
    overflow: hidden;
    background: var(--paper);
    box-shadow: 0 2px 10px rgba(0, 0, 0, 0.12);
  }
  .company-name {
    position: absolute;
    top: 44px;
    right: 44px;
    width: 190px;
    text-align: right;
    font-weight: 900;
    font-size: 22px;
    line-height: 1.1;
    text-transform: uppercase;
    color: var(--brand-red);
  }
  .anniversary-mark {
    position: absolute;
    left: 156px;
    top: 250px;
    width: 260px;
    height: 240px;
    border-radius: 40%;
    background: radial-gradient(ellipse at center, var(--mark-grey) 0%, var(--mark-red) 55%, rgba(255,255,255,0) 75%);
  }
  .footer {
    position: absolute;
    left: 32px;
    right: 32px;
    bottom: 30px;
    text-align: center;
    color: var(--brand-red);
  }
  .license {
    font-size: 10.5px;
    letter-spacing: 0.2px;
    text-transform: uppercase;
    margin-bottom: 6px;
  }
  .rule {
    height: 1px;
    background: var(--ink);
    margin-bottom: 6px;
  }
  .contact {
    font-size: 8.5px;
    white-space: nowrap;
  }
  .contact .sep { margin: 0 3px; }
</style>
</head>
<body>
  <main class="letterhead">
    <div class="company-name">Dorwin's Coating &amp; Renewal</div>

    <div class="anniversary-mark" role="img" aria-label="Faint anniversary mark: large outlined 25 with hand-lettered 'Years' and 'for over'"></div>

    <footer class="footer">
      <p class="license">License Number: KRT8046392</p>
      <div class="rule"></div>
      <p class="contact">(555) 413-2986<span class="sep">/</span>Dorwinrenewal@mailbrook.example<span class="sep">/</span>www.dorwinrenewal.example<span class="sep">/</span>4728 SW 81st Ter Halverd cove fl 39417</p>
    </footer>
  </main>
</body>
</html>
```